Velvet Lantern rebranding my business with a new business card

I have my new logo and now I need a refresher on my business cards. I really want something fun and fresh. I like black background or anything to make the color pop.
Logo
Name: Velvet Lantern
Contact Info as stated below:
Mira Pellow
555-013-4762
Logo
Name: Velvet Lantern
Mira Pellow
555-013-4762
fb.me/VelvetLanternbyMira
Instagram: @VelvetLanternbyMira

Industry/Entity Type

Business

Contact Information for Business Card

double-sided. Logo on one side. Contact info on the other.

Requirements
Must have
• Logo
• Name: Velvet Lantern
• Contact Info as stated below:
• Mira Pellow
• 555-013-4762
• fb.me/VelvetLanternbyMira
• fb.me/VelvetLanternbyMira

```html
<!DOCTYPE html>
<html lang="en">
<head>
<meta charset="utf-8">
<title>Velvet Lantern – Business Card</title>
<link href="https://fonts.googleapis.com/css2?family=Jost:wght@300;400&display=swap" rel="stylesheet">
<style>
  :root {
    --page: #ffffff;
    --ink: #0c0c0c;
    --wine: #7c1d17;
    --cream: #ffffff;
    --shade: rgba(0, 0, 0, 0.55);
  }
  html, body {
    margin: 0;
    padding: 0;
    width: 1200px;
    height: 1200px;
    overflow: hidden;
    background: var(--page);
  }
  .sheet {
    position: relative;
    width: 1200px;
    height: 1200px;
    font-family: "Jost", "Futura", sans-serif;
  }
  .card {
    position: absolute;
    left: 189px;
    width: 828px;
    height: 497px;
    overflow: hidden;
  }
  .card--front { top: 102px; background: var(--wine); }
  .card--back  { top: 644px; background: var(--wine); }
  .card__waves {
    position: absolute;
    inset: 0;
    width: 828px;
    height: 497px;
  }
  .wave-black { fill: var(--ink); filter: drop-shadow(0 4px 10px var(--shade)); }
  .mark-ring { fill: none; stroke: var(--cream); stroke-width: 3; }
  .brand-title {
    position: absolute;
    left: 340px;
    top: 92px;
    margin: 0;
    font-weight: 300;
    font-size: 52px;
    line-height: 1;
    letter-spacing: 2px;
    text-transform: uppercase;
    color: var(--cream);
    white-space: nowrap;
  }
  .contact {
    position: absolute;
    left: 467px;
    top: 268px;
    margin: 0;
    padding: 0;
    list-style: none;
    color: var(--cream);
    font-weight: 400;
    font-size: 16.5px;
    letter-spacing: 0.6px;
  }
  .contact__item {
    display: flex;
    align-items: center;
    height: 33px;
  }
  .contact__icon {
    width: 16px;
    height: 16px;
    margin-right: 11px;
    flex: none;
  }
  .contact__icon path, .contact__icon rect { fill: var(--cream); }
  .back-name {
    position: absolute;
    left: 0;
    width: 828px;
    top: 262px;
    margin: 0;
    text-align: center;
    font-weight: 300;
    font-size: 40px;
    letter-spacing: 2px;
    text-transform: uppercase;
    color: var(--cream);
  }
</style>
</head>
<body>
<main class="sheet">

  <section class="card card--front" aria-label="Business card front">
    <svg class="card__waves" viewBox="0 0 828 497" aria-hidden="true">
      <path class="wave-black" d="M0,0 H828 V90 C740,150 660,170 590,215 C500,270 500,420 260,430 C120,436 40,330 0,274 Z"/>
    </svg>
    <svg class="card__waves" viewBox="0 0 828 497" role="img" aria-label="Velvet Lantern brand mark area">
      <circle class="mark-ring" cx="215" cy="235" r="150"/>
    </svg>
    <h1 class="brand-title">Velvet Lantern</h1>
    <ul class="contact">
      <li class="contact__item">
        <svg class="contact__icon" viewBox="0 0 16 16" aria-hidden="true"><path d="M8 1 L15 8 H13 V15 H10 V10 H6 V15 H3 V8 H1 Z"/></svg>
        Mira Pellow
      </li>
      <li class="contact__item">
        <svg class="contact__icon" viewBox="0 0 16 16" aria-hidden="true"><path d="M3 1 L6 1 L7 5 L5 6.5 C6 9 7 10 9.5 11 L11 9 L15 10 L15 13 C15 14 14 15 13 15 C6 14 2 10 1 3 C1 2 2 1 3 1 Z"/></svg>
        555-013-4762
      </li>
      <li class="contact__item">
        <svg class="contact__icon" viewBox="0 0 16 16" aria-hidden="true"><rect x="2" y="2" width="12" height="12"/></svg>
        fb.me/VelvetLanternbyMira
      </li>
      <li class="contact__item">
        <svg class="contact__icon" viewBox="0 0 16 16" aria-hidden="true"><rect x="2" y="2" width="12" height="12"/></svg>
        @VelvetLanternbyMira
      </li>
    </ul>
  </section>

  <section class="card card--back" aria-label="Business card back">
    <svg class="card__waves" viewBox="0 0 828 497" aria-hidden="true">
      <path class="wave-black" d="M0,340 C80,300 180,330 300,380 C400,430 500,450 600,400 C700,350 760,300 828,244 V497 H0 Z"/>
    </svg>
    <svg class="card__waves" viewBox="0 0 828 497" role="img" aria-label="Velvet Lantern brand mark area">
      <circle class="mark-ring" cx="414" cy="160" r="80"/>
    </svg>
    <p class="back-name">Velvet Lantern</p>
  </section>

</main>
</body>
</html>
```